Digital Marketing Agency Landing Page

At VELIM, we offer a comprehensive solution for solar companies' client acquisition needs in the rapidly growing industry. We handle end-to-end client acquisition, meaning we manage the entire lifecycle of capturing new clients—from initial lead generation to delivering the ready-to-buy homeowner. Our expertise in targeted advertising, data analytics, and customer relationship management ensures that we not only find potential customers but also nurture them through tailored engagement strategies until they are ready to make a purchase. By entrusting us with your client acquisition process, solar companies can focus on what they do best—providing sustainable energy solutions—while we work behind the scenes to grow your customer base and increase your market share.

We need to restructure our website to make it more professional. We don't need any complex functionalities. We are looking for someone that is good in design and can build a visually aesthetic website following our brand image. We only need a landing page and a lead form in the end. I would like to have only one page, but a relatively big one where people scroll down. I would like to have a minimal and classy look. Something that is timeless and elegant.

Structure:

initial page
About us
How we operate
Get in touch

Target Market(s)

Solar Comapanies

Industry/Entity Type

Marketing solautions

Coding

Coded - Design and coding required

Number of Pages Required

1 page

Requirements
Nice to have
• Inspirations: https://www.qz.zu/ https://www.marchbeck.example/ https://www.tovanrid.example/ https://pruvo.example/

```html
<!DOCTYPE html>
<html lang="en">
<head>
<meta charset="utf-8">
<title>VELIM — Digital Marketing for Solar Companies</title>
<link href="https://fonts.googleapis.com/css2?family=Montserrat:wght@400;500;600;700&family=Libre+Franklin:wght@400;500&display=swap" rel="stylesheet">
<style>
:root{
  --ink:#10202b;
  --white:#ffffff;
  --text:#1d1d1d;
  --muted:#444;
  --footer:#000000;
  --line:#c9c9c9;
  --placeholder:#e3e5e8;
}
*{box-sizing:border-box;margin:0;padding:0}
html,body{width:1200px;height:2278px;overflow:hidden}
body{position:relative;background:var(--white);font-family:"Libre Franklin",Arial,sans-serif;color:var(--text)}
.abs{position:absolute}
.heading{font-family:"Montserrat",Arial,sans-serif;font-weight:600;color:var(--ink)}
.btn{position:absolute;display:flex;align-items:center;justify-content:center;font-family:"Montserrat",Arial,sans-serif;font-weight:600;font-size:16px;border-radius:2px}
.btn-dark{background:var(--ink);color:var(--white);box-shadow:3px 3px 6px rgba(0,0,0,.25)}
.btn-light{background:var(--white);color:var(--ink)}

/* header */
.site-header{position:absolute;left:0;top:0;width:1200px;height:87px;background:var(--white)}
.brand{left:99px;top:22px;height:42px;display:flex;align-items:center;font-family:"Montserrat",Arial,sans-serif;font-weight:400;font-size:33px;color:var(--ink);letter-spacing:1px}
.nav a{position:absolute;top:33px;font-family:"Montserrat",Arial,sans-serif;font-size:15px;color:#333;text-decoration:none}
.nav a.active{color:var(--ink);font-weight:600;text-decoration:underline;text-underline-offset:4px}

/* hero */
.hero{position:absolute;left:0;top:87px;width:1200px;height:588px}
.hero-photo{position:absolute;inset:0;background:linear-gradient(100deg,#2a2a24 0%,#3b3a2c 30%,#6b6a5c 48%,#2f4256 62%,#1e4a6e 80%,#3d6f92 100%)}
.hero-shade{position:absolute;inset:0;background:linear-gradient(90deg,rgba(0,0,0,.45),rgba(0,0,0,0) 70%)}
.hero-dots span{position:absolute;left:47px;width:9px;height:9px;border-radius:50%;background:rgba(255,255,255,.55)}
.hero-dots span:first-child{background:var(--white)}
.hero-title{left:99px;top:165px;font-family:"Montserrat",Arial,sans-serif;font-weight:700;font-size:53px;line-height:56px;color:var(--white);letter-spacing:1px}
.hero-text{left:99px;top:283px;width:520px;font-size:15px;line-height:31px;color:var(--white)}
.contact-card{left:660px;top:83px;width:441px;height:422px;background:rgba(255,255,255,.93)}
.contact-card h2{position:absolute;top:36px;width:100%;text-align:center;font-size:32px;font-weight:600}
.field{position:absolute;left:30px;width:381px;border:1px solid #333;border-radius:2px;padding:15px 15px;font-size:15px;color:#333;font-family:"Libre Franklin",Arial,sans-serif}

/* about */
.about-pattern{left:76px;top:722px;width:110px;height:82px;background:var(--placeholder)}
.about-photo{left:108px;top:754px;width:445px;height:435px;background:linear-gradient(135deg,#e9e7e2 0%,#f4f3ef 40%,#c9ccc9 70%,#5a6a80 100%)}
.about-frame{left:116px;top:765px;width:450px;height:438px;border:3px solid var(--ink);border-radius:2px}
.about-title{left:600px;top:750px;font-size:31px;letter-spacing:.5px}
.about-text{left:600px;top:795px;width:500px;font-size:15px;line-height:30.9px;color:var(--muted)}

/* services */
.services{position:absolute;left:0;top:1285px;width:1200px;height:566px;background:linear-gradient(135deg,#efeff1,#e4e4e7 50%,#ececee)}
.services h2{position:absolute;top:58px;width:100%;text-align:center;font-size:31px;letter-spacing:.5px}
.service-card{position:absolute;top:128px;width:317px;height:364px;border-radius:6px;overflow:hidden}
.service-card::after{content:"";position:absolute;inset:0;background:linear-gradient(180deg,rgba(0,0,0,0) 50%,rgba(10,15,20,.75))}
.service-card .label{position:absolute;left:0;right:0;bottom:42px;z-index:1;text-align:center;color:var(--white);font-family:"Montserrat",Arial,sans-serif;font-weight:700;font-size:21px;line-height:31px}

/* footer */
.site-footer{position:absolute;left:0;top:1851px;width:1200px;height:427px;background:var(--footer);color:var(--white)}
.site-footer h3{position:absolute;top:60px;font-family:"Montserrat",Arial,sans-serif;font-weight:600;font-size:21px}
.links{position:absolute;top:98px;list-style:none}
.links li{height:31px;display:flex;align-items:center;font-size:15px}
.links svg{margin-right:10px}
.contact-item{position:absolute;left:507px;display:flex;align-items:center;font-size:15px}
.contact-item .icon{width:37px;height:37px;border-radius:50%;background:var(--white);display:flex;align-items:center;justify-content:center;margin-right:11px}
.newsletter-text{left:828px;top:108px;width:290px;font-size:15px;line-height:31px}
.newsletter-field{left:831px;top:180px;width:270px;height:30px;border-bottom:2px solid var(--white);font-size:15px}
.footer-rule{left:99px;top:365px;width:1002px;height:1px;background:var(--line)}
.copyright{top:383px;width:100%;text-align:center;font-family:"Montserrat",Arial,sans-serif;font-size:15px}
</style>
</head>
<body>

<header class="site-header">
  <div class="abs brand">VELIM</div>
  <nav class="nav">
    <a class="active" style="left:661px">Home</a>
    <a style="left:755px">About Us</a>
    <a style="left:871px">Services</a>
  </nav>
  <a class="btn btn-dark" style="left:965px;top:18px;width:136px;height:50px">Contact Us</a>
</header>

<section class="hero">
  <div class="hero-photo" role="img" aria-label="Rows of solar panels across a hillside at sunset"></div>
  <div class="hero-shade"></div>
  <div class="hero-dots">
    <span style="top:238px"></span><span style="top:261px"></span><span style="top:283px"></span><span style="top:307px"></span>
  </div>
  <h1 class="abs hero-title">WELCOME TO<br>VELIM</h1>
  <p class="abs hero-text">Lorem ipsum dolor sit amet, consectetur adipiscing elit, sed do eiusmod tempor incididunt ut labore et dolore magna aliqua.</p>
  <a class="btn btn-light" style="left:99px;top:360px;width:136px;height:52px">Get Started</a>

  <form class="abs contact-card">
    <h2 class="heading">CONTACT US</h2>
    <div class="field" style="top:92px;height:48px">Enter Name</div>
    <div class="field" style="top:157px;height:48px">Enter Email</div>
    <div class="field" style="top:222px;height:94px">Message</div>
    <div class="btn btn-dark" style="left:30px;top:333px;width:381px;height:49px;box-shadow:none;font-size:18px">Submit</div>
  </form>
</section>

<section class="about">
  <div class="abs about-pattern" role="img" aria-label="Decorative dot pattern"></div>
  <div class="abs about-frame"></div>
  <div class="abs about-photo" role="img" aria-label="Analyst working at a desk with data charts on a monitor in a bright office"></div>
  <h2 class="abs heading about-title">ABOUT US</h2>
  <p class="abs about-text">Sed ut perspiciatis unde omnis iste natus error sit voluptatem accusantium doloremque laudantium, totam rem aperiam, eaque ipsa quae ab illo inventore veritatis et quasi architecto beatae vitae dicta sunt explicabo. Nemo enim ipsam voluptatem quia voluptas sit aspernatur aut odit aut fugit, sed quia consequuntur magni dolores eos qui ratione voluptatem sequi nesciunt. Neque porro quisquam est, qui dolorem ipsum quia dolor sit amet, consectetur, adipisci velit, sed quia non numquam eius modi tempora incidunt ut labore et dolore magnam aliquam quaerat voluptatem. Ut enim ad minima veniam, quis nostrum exercitationem ullam corporis suscipit laboriosam, nisi ut aliquid ex ea commodi consequatur?</p>
  <a class="btn btn-dark" style="left:600px;top:1148px;width:137px;height:51px">Contact Us</a>
</section>

<section class="services">
  <h2 class="heading">OUR SERVICES</h2>
  <div class="service-card" style="left:99px;background:linear-gradient(160deg,#b9b9b9,#6e6e6e 50%,#2e2e2e)" role="img" aria-label="Designer working on an advertising layout at a studio desk">
    <div class="label">Advertising</div>
  </div>
  <div class="service-card" style="left:441px;background:linear-gradient(160deg,#d9dadc,#8d949c 50%,#3a3f45)" role="img" aria-label="Team meeting around a table reviewing data charts">
    <div class="label">Data Analytics</div>
  </div>
  <div class="service-card" style="left:784px;background:linear-gradient(160deg,#7e8a96,#4c5866 50%,#1f2832)" role="img" aria-label="Colleagues in conversation in a modern office">
    <div class="label">Customer Relationship<br>Management</div>
  </div>
</section>

<footer class="site-footer">
  <h3 style="left:97px">Quick Links</h3>
  <ul class="links" style="left:99px">
    <li><svg width="15" height="14" viewBox="0 0 15 14"><path d="M1 7h11M7 2l5 5-5 5" stroke="#fff" stroke-width="2.6" fill="none"/></svg>Home</li>
    <li><svg width="15" height="14" viewBox="0 0 15 14"><path d="M1 7h11M7 2l5 5-5 5" stroke="#fff" stroke-width="2.6" fill="none"/></svg>About Us</li>
    <li><svg width="15" height="14" viewBox="0 0 15 14"><path d="M1 7h11M7 2l5 5-5 5" stroke="#fff" stroke-width="2.6" fill="none"/></svg>Services</li>
    <li><svg width="15" height="14" viewBox="0 0 15 14"><path d="M1 7h11M7 2l5 5-5 5" stroke="#fff" stroke-width="2.6" fill="none"/></svg>Contact Us</li>
  </ul>

  <h3 style="left:297px">Other Links</h3>
  <ul class="links" style="left:298px">
    <li><svg width="15" height="14" viewBox="0 0 15 14"><path d="M1 7h11M7 2l5 5-5 5" stroke="#fff" stroke-width="2.6" fill="none"/></svg>FAQ</li>
    <li><svg width="15" height="14" viewBox="0 0 15 14"><path d="M1 7h11M7 2l5 5-5 5" stroke="#fff" stroke-width="2.6" fill="none"/></svg>Tems of Use</li>
    <li><svg width="15" height="14" viewBox="0 0 15 14"><path d="M1 7h11M7 2l5 5-5 5" stroke="#fff" stroke-width="2.6" fill="none"/></svg>Privacy Policy</li>
    <li><svg width="15" height="14" viewBox="0 0 15 14"><path d="M1 7h11M7 2l5 5-5 5" stroke="#fff" stroke-width="2.6" fill="none"/></svg>Support Links</li>
    <li><svg width="15" height="14" viewBox="0 0 15 14"><path d="M1 7h11M7 2l5 5-5 5" stroke="#fff" stroke-width="2.6" fill="none"/></svg>Conditions</li>
  </ul>

  <h3 style="left:507px">Contact Us</h3>
  <div class="contact-item" style="top:108px">
    <span class="icon"><svg width="12" height="16" viewBox="0 0 12 16"><path d="M6 0a6 6 0 0 0-6 6c0 4.5 6 10 6 10s6-5.5 6-10a6 6 0 0 0-6-6z" fill="#10202b"/><circle cx="6" cy="6" r="2.2" fill="#fff"/></svg></span>Velim.United State.
  </div>
  <div class="contact-item" style="top:168px">
    <span class="icon"><svg width="16" height="12" viewBox="0 0 16 12"><rect width="16" height="12" rx="1.5" fill="#10202b"/><path d="M1 1.5l7 5 7-5" stroke="#fff" stroke-width="1.4" fill="none"/></svg></span>info@velim.example
  </div>
  <div class="contact-item" style="top:228px">
    <span class="icon"><svg width="15" height="15" viewBox="0 0 24 24"><path d="M6.6 10.8a15.1 15.1 0 0 0 6.6 6.6l2.2-2.2a1 1 0 0 1 1-.25 11.4 11.4 0 0 0 3.6.57 1 1 0 0 1 1 1V20a1 1 0 0 1-1 1A17 17 0 0 1 3 4a1 1 0 0 1 1-1h3.5a1 1 0 0 1 1 1c0 1.25.2 2.45.57 3.57a1 1 0 0 1-.25 1z" fill="#10202b"/></svg></span>+1 555 010 0199
  </div>

  <h3 style="left:827px">Sign Up Our Newsletter</h3>
  <p class="abs newsletter-text">Lorem ipsum dolor sit amet,consectetur adipiscing elit,adipiscing elit.</p>
  <div class="abs newsletter-field">Email</div>
  <div class="btn btn-light" style="left:835px;top:241px;width:137px;height:51px;font-size:18px">Subscribe</div>

  <div class="abs footer-rule"></div>
  <p class="abs copyright">Copyrights@2023.Velim.All Rights Reserved</p>
</footer>

</body>
</html>
```